Redesign This Psychology Website

We would like a slight redesign of this successful psychology (relationship counselling) website:

www.TheKelvaleClinic.com.au

We are updating the website, and we'd like a slight refresh of the design and style.

Please keep to very similar colours, and use the same logo. We're looking for around 10 page templates, however the main one is the home page.

Keep in mind, this website already converts quite well, so we want a new, fresh design in keeping with this one. Please don't bother designing something too extremely different.

thanks :)

Target Market(s)

couples who are looking for relationship counselling. Men and women, 25 - 70, across Australia

Industry/Entity Type

Psychology

Number of Pages Required

5+ page

Font styles to use
Sans Serif

Colors
87cfc6
b7a5cd
ec1f27
ffffff
cee9f5

Requirements
Must have
• a similar look to the current design, just looking for a slight refresh.
• Search bar
• Areas for lots of photos
• same logo
• lots of content areas
Nice to have
• great content areas, where we can display a lot of content and our areas.
Should not have
• no colors like orange, etc.
• should not have a totally different feel.

```html
<!DOCTYPE html>
<html lang="en">
<head>
<meta charset="utf-8">
<title>The Kelvale Clinic – Shop</title>
<link href="https://fonts.googleapis.com/css2?family=Raleway:wght@400;500;600&family=Mulish:wght@400;600;700&display=swap" rel="stylesheet">
<style>
:root{
  --teal:#87cfc6;
  --teal-deep:#1f8a8a;
  --teal-dark:#177a80;
  --lilac:#b7a5cd;
  --red:#ec1f27;
  --white:#ffffff;
  --ink:#333333;
  --grey:#777777;
  --line:#dddddd;
  --bar:#f3f3f3;
}
*{margin:0;padding:0;box-sizing:border-box}
html,body{width:804px;height:1200px;overflow:hidden;background:var(--white)}
body{font-family:'Mulish',sans-serif;color:var(--ink)}
.page{position:relative;width:804px;height:1200px;overflow:hidden}
.abs{position:absolute}

.topbar{left:0;top:0;width:804px;height:26px;background:var(--bar);border-bottom:1px solid #e4e4e4;font-size:10px;color:var(--grey)}
.topbar .invite{left:98px;top:7px}
.toplinks{right:94px;top:0;display:flex;height:26px}
.toplinks span{padding:0 8px;line-height:26px;border-left:1px solid #e0e0e0}
.toplinks span:first-child{border-left:none}

.brand{display:flex;align-items:center;gap:8px}
.brand-dot{width:30px;height:30px;border-radius:50%;background:var(--teal-deep)}
.brand-name{font-family:'Raleway',sans-serif;font-size:19px;font-weight:500;color:var(--teal-deep);line-height:1}
.brand-tag{font-size:8.5px;color:var(--teal-deep);margin-top:4px}
.header-brand{left:88px;top:48px}

.search{left:317px;top:57px;width:237px;height:26px;border:1px solid #d6d6d6;border-radius:2px;font-size:9px;color:#999;display:flex;align-items:center;padding-left:20px}
.search svg{position:absolute;left:6px;top:7px}

.callout{right:89px;top:53px;text-align:right}
.callout .label{font-size:11px;color:var(--teal)}
.callout .phone{font-size:15.5px;font-weight:600;color:var(--teal-dark);display:flex;align-items:center;gap:3px;margin-top:2px}

.nav{left:0;top:109px;width:804px;height:44px;background:linear-gradient(#96d6cd,#7dc9c0);display:flex;padding-left:88px}
.nav a{font-family:'Raleway',sans-serif;font-weight:500;font-size:10.5px;color:var(--white);text-decoration:none;text-align:center;display:flex;align-items:center;justify-content:center;line-height:1.15;border-right:1px solid rgba(255,255,255,.35);padding:0 6px}
.nav a:last-child{border-right:none}

.hero{left:0;top:153px;width:804px;height:219px;
  background:
    radial-gradient(ellipse 160px 150px at 270px 110px,rgba(214,170,140,.55),transparent 70%),
    radial-gradient(ellipse 150px 140px at 430px 120px,rgba(190,120,110,.45),transparent 70%),
    linear-gradient(100deg,#9a8878 0%,#bfa88f 30%,#d8c7b4 55%,#e6ded4 80%,#d9d3cc 100%)}
.hero-title{left:85px;top:265px;font-family:'Raleway',sans-serif;font-weight:600;font-size:24px;color:var(--white);letter-spacing:.5px}

.shop-title{left:91px;top:410px;font-family:'Raleway',sans-serif;font-weight:400;font-size:20px;color:var(--ink)}
.shop-sub{left:91px;top:439px;font-size:11.5px;color:var(--grey)}

.product{width:169px;height:212px;border:1px solid var(--line);background:var(--white)}
.product .shot{position:absolute;left:46px;top:27px;width:76px;height:106px;box-shadow:2px 3px 6px rgba(0,0,0,.18)}
.product .name{position:absolute;left:11px;top:158px;font-size:11.5px;color:var(--ink);line-height:14px}
.product .price{position:absolute;left:11px;top:178px;font-size:13px;color:var(--teal-dark);line-height:16px}
.product .cart{position:absolute;right:7px;top:174px;width:71px;height:20px;background:var(--red);color:var(--white);font-size:8.5px;font-weight:700;display:flex;align-items:center;justify-content:center}

.promo{left:509px;width:205px;height:158px;border:1px solid #e2e2e2;background:var(--white);overflow:hidden;box-shadow:0 1px 2px rgba(0,0,0,.08)}
.promo .shot{position:absolute;right:0;top:0;width:92px;height:158px;clip-path:polygon(38% 0,100% 0,100% 100%,0 100%)}
.promo h3{position:absolute;left:17px;top:17px;font-family:'Raleway',sans-serif;font-weight:500;font-size:13px;line-height:1.3;color:var(--ink)}
.promo p{position:absolute;left:18px;top:56px;width:96px;font-size:7px;line-height:13px;color:var(--grey)}
.promo .more{position:absolute;left:18px;top:117px;width:64px;height:18px;background:var(--lilac);color:var(--white);font-size:7px;display:flex;align-items:center;justify-content:center}

.footer{left:0;top:952px;width:804px;height:200px;background:linear-gradient(#ececec,#fafafa 25%,#fafafa)}
.footer-brand{left:94px;top:1005px}
.fcol{top:996px}
.fcol h4{font-family:'Raleway',sans-serif;font-weight:600;font-size:11px;color:var(--teal-dark);margin-bottom:9px}
.fcol li{list-style:none;font-size:8.5px;color:var(--grey);line-height:18.4px}
.socials{display:flex;gap:6px;margin-top:8px}
.socials span{width:22px;height:22px;border-radius:50%;background:var(--teal-dark)}
.socials span:nth-child(odd){background:var(--teal)}
.copy{left:0;top:1152px;width:804px;height:48px;background:#ececec;font-size:8.5px;color:var(--grey);text-align:center;line-height:48px}
</style>
</head>
<body>
<div class="page">

  <div class="abs topbar">
    <span class="abs invite">Join Our Assoicate Program →</span>
    <div class="abs toplinks"><span>Home</span><span>Cart</span><span>Blog</span><span>Resources</span><span>Contact</span></div>
  </div>

  <div class="abs brand header-brand">
    <span class="brand-dot"></span>
    <div><div class="brand-name">The Kelvale Clinic</div><div class="brand-tag">helping you create loving relationships</div></div>
  </div>

  <div class="abs search">
    <svg width="11" height="11" viewBox="0 0 11 11"><circle cx="4.5" cy="4.5" r="3.5" fill="none" stroke="#bbb" stroke-width="1.2"/><line x1="7" y1="7" x2="10" y2="10" stroke="#bbb" stroke-width="1.2"/></svg>
    Search here
  </div>

  <div class="abs callout">
    <div class="label">Call Us Now</div>
    <div class="phone">
      <svg width="16" height="16" viewBox="0 0 16 16"><path d="M3 1.5l3 .5 1 3.5-2 1.5a9 9 0 0 0 4 4l1.5-2 3.5 1 .5 3-2 1.5C7 14 2 9 1.5 3.5z" fill="none" stroke="#ec1f27" stroke-width="1.2" stroke-linejoin="round"/></svg>
      1300 555 014
    </div>
  </div>

  <nav class="abs nav">
    <a style="width:90px">COUNSELLING<br>TYPES</a>
    <a style="width:178px">RELATIONSHIP COUNSELLING<br>LOCATIONS</a>
    <a style="width:91px">SEX THERAPY<br>LOCATIONS</a>
    <a style="width:75px">ABOUT US</a>
    <a style="width:70px">QUIZZES</a>
    <a style="width:68px">FAQ'S</a>
    <a style="width:70px">CONTACT</a>
  </nav>

  <div class="abs hero" role="img" aria-label="Smiling couple looking at a laptop together in a bright kitchen"></div>
  <div class="abs hero-title">SHOP NOW</div>

  <h1 class="abs shop-title">Shop</h1>
  <div class="abs shop-sub">Showing the single result</div>

  <div class="abs product" style="left:88px;top:463px">
    <div class="shot" style="left:46px;top:27px;width:74px;height:104px;background:linear-gradient(#ead2b6,#dba792 60%,#c44c7c 88%,#c0336e)" role="img" aria-label="Book cover"></div>
    <div class="name">Night For Us</div><div class="price">$9.95</div><div class="cart">Add to Cart</div>
  </div>
  <div class="abs product" style="left:274px;top:463px">
    <div class="shot" style="left:40px;top:30px;width:62px;height:96px;background:linear-gradient(90deg,#1a1a1a,#4a4a4a)" role="img" aria-label="Book box with a disc"></div>
    <div class="name">Night For Us</div><div class="price">$9.95</div><div class="cart">Add to Cart</div>
  </div>
  <div class="abs product" style="left:87px;top:691px">
    <div class="shot" style="left:46px;top:36px;width:70px;height:102px;background:linear-gradient(90deg,#ececec,#fafafa 40%,#dcdcdc)" role="img" aria-label="Blank white product box"></div>
    <div class="name">Night For Us</div><div class="price">$9.95</div><div class="cart">Add to Cart</div>
  </div>
  <div class="abs product" style="left:273px;top:692px">
    <div class="shot" style="left:46px;top:36px;width:70px;height:102px;background:linear-gradient(90deg,#ececec,#fafafa 40%,#dcdcdc)" role="img" aria-label="Blank white product box"></div>
    <div class="name">Night For Us</div><div class="price">$9.95</div><div class="cart">Add to Cart</div>
  </div>

  <div class="abs promo" style="top:421px">
    <div class="shot" style="background:linear-gradient(#f0c7d4,#f4a55a 55%,#7a3a1a)" role="img" aria-label="Two hands reaching toward each other at sunset"></div>
    <h3>Rebates<br>Available</h3>
    <p>Maecenas aliquet velit vel turpis Mauris neque metus malesuada nec ultricies sit amet</p>
    <div class="more">Learn More</div>
  </div>
  <div class="abs promo" style="top:594px">
    <div class="shot" style="background:linear-gradient(#e6eef2,#cfd9de)" role="img" aria-label="Doctor in a white coat with a stethoscope"></div>
    <h3>GP Referral<br>Info</h3>
    <p>Maecenas aliquet velit vel turpis Mauris neque metus malesuada nec ultricies sit amet</p>
    <div class="more">Learn More</div>
  </div>
  <div class="abs promo" style="top:768px">
    <div class="shot" style="background:linear-gradient(#2d3a3c,#1a2224)" role="img" aria-label="Man resting his head in his hand looking worried"></div>
    <h3>Anxiety and<br>Depression</h3>
    <p>Maecenas aliquet velit vel turpis Mauris neque metus malesuada nec ultricies sit amet</p>
    <div class="more">Learn More</div>
  </div>

  <footer class="abs footer"></footer>
  <div class="abs brand footer-brand">
    <span class="brand-dot"></span>
    <div><div class="brand-name">The Kelvale Clinic</div><div class="brand-tag">helping you create loving relationships</div></div>
  </div>
  <div class="abs fcol" style="left:309px">
    <h4>QUICK LINKS</h4>
    <ul><li>Home</li><li>About Us</li><li>Our Blogs</li><li>Shop Cart</li><li>Contact Us</li></ul>
  </div>
  <div class="abs fcol" style="left:421px">
    <h4>RESOURCES</h4>
    <ul><li>Counselling Type</li><li>Sex Therapy</li><li>Quizzes</li><li>FAQ</li><li>Relationship Counselling</li></ul>
  </div>
  <div class="abs fcol" style="left:558px">
    <h4>CONTACT US</h4>
    <ul><li>412 Harbour Street Suite 12</li><li>1300 555 014</li><li>Email: info@kelvaleclinic.com</li></ul>
    <div class="socials"><span></span><span></span><span></span><span></span></div>
  </div>
  <div class="abs copy">© 2017 Company Name &nbsp;All right reserved</div>

</div>
</body>
</html>
```